Moravel Aesthetic Doctor

I require an elegant, luxurious looking business card for my aesthetic business. I am a doctor and that will set me aside from competitors. I am planning to provide home and spa based treatments to clients with high expectations. I have attached my logo.

```html
<!DOCTYPE html>
<html lang="en">
<head>
<meta charset="utf-8">
<title>Moravel Aesthetic Doctor — Business Card</title>
<link href="https://fonts.googleapis.com/css2?family=Mulish:wght@300;400;600&display=swap" rel="stylesheet">
<style>
  :root {
    --backdrop: #d9d9db;
    --card: #ffffff;
    --ink-grey: #8a8c8f;
    --ink-dark: #5f6164;
    --accent: #29b6e6;
    --swoosh-light: #ececed;
    --swoosh-mid: #dcdcde;
  }
  * { margin: 0; padding: 0; box-sizing: border-box; }
  html, body { width: 1200px; height: 1007px; overflow: hidden; }
  body {
    background: var(--backdrop);
    font-family: "Mulish", sans-serif;
    display: flex;
    align-items: center;
    justify-content: center;
    gap: 40px;
  }
  .card {
    position: relative;
    width: 540px;
    height: 309px;
    background: var(--card);
    box-shadow: 0 10px 30px rgba(0,0,0,0.12);
    overflow: hidden;
  }

  /* Info side */
  .info { padding: 52px 40px 0 48px; color: var(--ink-grey); }
  .info__name { font-size: 25px; font-weight: 300; color: var(--ink-dark); }
  .info__cred { font-size: 12px; font-weight: 400; color: var(--accent); margin-left: 4px; letter-spacing: .5px; }
  .info__diploma { font-size: 12.5px; font-weight: 300; margin-top: 4px; }
  .info__body { display: flex; margin-top: 34px; }
  .info__services { font-size: 13.5px; font-weight: 300; line-height: 1.7; flex: 1; }
  .info__services .dot { color: var(--accent); margin: 0 4px; }
  .info__contact {
    border-left: 1px solid #c8c9cb;
    padding-left: 14px;
    margin-left: 14px;
    font-size: 12.5px;
    font-weight: 300;
    line-height: 1.9;
    white-space: nowrap;
    align-self: flex-start;
    margin-top: -64px;
  }
  .info__contact li { list-style: none; display: flex; align-items: center; gap: 7px; }
  .info__contact svg { width: 11px; height: 11px; fill: var(--accent); }

  /* Brand side */
  .brand__pattern {
    position: absolute; inset: 0;
    background:
      radial-gradient(ellipse at 75% 45%, var(--swoosh-mid) 0%, transparent 60%),
      linear-gradient(160deg, var(--card) 20%, var(--swoosh-light) 55%, var(--swoosh-mid) 100%);
  }
  .brand__logo {
    position: absolute; left: 60px; top: 88px;
    display: flex; align-items: center; gap: 14px;
  }
  .brand__mark { width: 40px; height: 40px; border-radius: 50%; background: var(--accent); }
  .brand__name {
    font-size: 26px; font-weight: 300; color: var(--accent);
    letter-spacing: 3px; line-height: 1.1; text-transform: uppercase;
  }
  .brand__tagline {
    position: absolute; left: 116px; top: 180px;
    font-size: 13px; font-weight: 400; color: var(--ink-dark);
  }
</style>
</head>
<body>

  <section class="card info">
    <h1 class="info__name">Dr Elise Varnholt<span class="info__cred">MRCPCH MD</span></h1>
    <p class="info__diploma">Australasian Diploma of Aesthetic Medicine</p>
    <div class="info__body">
      <p class="info__services">
        Dermal injectables<span class="dot">•</span>Plasma facials<span class="dot">•</span>Microneedling<span class="dot">•</span>Skin boosters<br>
        Excessive sweating<span class="dot">•</span>Home and Spa Based Treatments
      </p>
      <ul class="info__contact">
        <li><svg viewBox="0 0 24 24"><path d="M6.6 10.8a15 15 0 0 0 6.6 6.6l2.2-2.2c.3-.3.7-.4 1-.2 1.1.4 2.3.6 3.6.6.6 0 1 .4 1 1V20c0 .6-.4 1-1 1A17 17 0 0 1 3 4c0-.6.4-1 1-1h3.5c.6 0 1 .4 1 1 0 1.3.2 2.5.6 3.6.1.3 0 .7-.2 1z"/></svg>0800 555 014</li>
        <li><svg viewBox="0 0 24 24"><path d="M2 5h20v14H2zm2 2v.5l8 5 8-5V7l-8 5z"/></svg>elise@moravel.co.nz</li>
        <li><svg viewBox="0 0 24 24"><circle cx="12" cy="12" r="10"/></svg>www.moravel.co.nz</li>
      </ul>
    </div>
  </section>

  <section class="card brand">
    <div class="brand__pattern" role="img" aria-label="Soft white flowing swoosh decoration on pale grey"></div>
    <div class="brand__logo">
      <span class="brand__mark"></span>
      <p class="brand__name">Moravel<br>Aesthetic Doctor</p>
    </div>
    <p class="brand__tagline">Home and Spa Based Treatments</p>
  </section>

</body>
</html>
```